Family Owned and Operated Spray Foam Insulation Company needs a business card design

We're a new company based in the heart of Texas (Fort Worth). We spray foam insulation into residential houses, commercial buildings, metal buildings, etc. Spray foam insulation provides a huge reduction in energy/costs so that is what drives our market. We like the primary colors but are open to suggestions and are coming to the experts for some creativity. I'm attaching a picture of shirt mock up we have with KBL on the front to show what we were leaning towards as well as some business cards that I find striking and memorable. I'm looking for a card that is clean and professional with a bit of edge. Note: My computer won't pull up the color samples below for me to choose so it's in your hands.

Target Market(s)

Professional custom home builders, construction industry, home owners

Industry/Entity Type

Residential

Contact Information for Business Card

Name: Martin Kestrel (no title) Phone #: 817-555-0148, address: 4087 larkspur ave fort worth tx 76110, email: martin@kblinsulation.example, website: kblinsulation.example

Requirements
Must have
• We want the words KBL and Kestrel Spray Foam Insulation showcased on the card but hopefully on opposite sides
Should not have
• Any type of spray foam gun or splatter clip art

```html
<!DOCTYPE html>
<html lang="en">
<head>
<meta charset="utf-8">
<title>Kestrel Spray Foam Insulation – Business Card</title>
<link href="https://fonts.googleapis.com/css2?family=Lobster&family=Arimo:wght@400;700&display=swap" rel="stylesheet">
<style>
  :root {
    --page-bg: #e9e6e1;
    --brand-blue: #6a90d2;
    --band-blue: #6387cc;
    --band-blue-light: #7aa0dc;
    --accent-red: #e4393c;
    --card-white: #fbfbfb;
    --faint-blue: #e6e9f0;
    --ink-blue: #5a82c8;
  }
  * { margin: 0; padding: 0; box-sizing: border-box; }
  html, body { width: 1200px; height: 885px; overflow: hidden; }
  body {
    background: var(--page-bg);
    display: flex;
    flex-direction: column;
    align-items: center;
    justify-content: center;
    gap: 60px;
    font-family: "Arimo", Arial, sans-serif;
  }
  .card {
    width: 580px;
    height: 331px;
    background: var(--card-white);
    box-shadow: 0 6px 18px rgba(0,0,0,0.18);
    position: relative;
    overflow: hidden;
  }

  /* Front */
  .card-front { display: flex; flex-direction: column; }
  .top-band {
    height: 96px;
    background: linear-gradient(180deg, var(--band-blue-light), var(--band-blue));
    border-bottom: 5px solid var(--accent-red);
    display: flex; align-items: center; justify-content: center;
  }
  .company-name {
    font-family: "Lobster", cursive;
    color: #fff;
    font-size: 42px;
    letter-spacing: 0.5px;
    white-space: nowrap;
  }
  .middle {
    flex: 1;
    display: flex;
    align-items: center;
    padding: 0 36px 0 40px;
    justify-content: space-between;
  }
  .wordmark {
    font-family: "Arimo", Arial, sans-serif;
    font-weight: 700;
    color: var(--brand-blue);
    font-size: 100px;
    letter-spacing: 2px;
    line-height: 1;
  }
  .contact { text-align: right; color: var(--ink-blue); }
  .person-name {
    font-family: "Lobster", cursive;
    font-size: 32px;
    margin-bottom: 8px;
  }
  .contact-line { font-size: 17px; line-height: 1.35; white-space: nowrap; }
  .bottom-band {
    height: 58px;
    background: var(--band-blue);
    border-top: 5px solid var(--accent-red);
    display: flex; align-items: center; justify-content: center;
    color: #fff;
    font-size: 20px;
    letter-spacing: 1px;
    text-transform: uppercase;
    white-space: nowrap;
  }

  /* Back */
  .card-back {
    display: flex; flex-direction: column;
    align-items: center; justify-content: center;
    background: linear-gradient(135deg, #fdfdfd, #eeeff2);
  }
  .faint-mark {
    position: absolute;
    inset: 0;
    display: flex; align-items: center; justify-content: center;
    font-weight: 700;
    font-size: 230px;
    line-height: 1;
    color: var(--faint-blue);
    letter-spacing: 4px;
  }
  .back-wordmark { position: relative; font-size: 116px; }
  .back-name {
    position: relative;
    font-family: "Lobster", cursive;
    color: var(--ink-blue);
    font-size: 30px;
    margin-top: 8px;
  }
</style>
</head>
<body>
  <section class="card card-front">
    <div class="top-band"><span class="company-name">Kestrel Spray Foam Insulation</span></div>
    <div class="middle">
      <div class="wordmark">KBL</div>
      <div class="contact">
        <div class="person-name">Martin Kestrel</div>
        <div class="contact-line">555-555-0148</div>
        <div class="contact-line">martin@kblinsulation.example</div>
        <div class="contact-line">kblinsulation.example</div>
      </div>
    </div>
    <div class="bottom-band">4087 Larkspur Ave Brenmoor TX 79990</div>
  </section>

  <section class="card card-back">
    <div class="faint-mark" aria-hidden="true">KBL</div>
    <div class="wordmark back-wordmark">KBL</div>
    <div class="back-name">Kestrel Spray Foam Insulation</div>
  </section>
</body>
</html>
```